Moravel Aesthetic Doctor

I require an elegant, luxurious looking business card for my aesthetic business. I am a doctor and that will set me aside from competitors. I am planning to provide home and spa based treatments to clients with high expectations. I have attached my logo.

```html
<!DOCTYPE html>
<html lang="en">
<head>
<meta charset="utf-8">
<title>Moravel Aesthetic Doctor — Business Card</title>
<link href="https://fonts.googleapis.com/css2?family=Montserrat:wght@300;400;500&display=swap" rel="stylesheet">
<style>
  :root {
    --backdrop: #2bb5e6;
    --card: #ffffff;
    --brand-blue: #36ade3;
    --ink: #3a3a3c;
    --ink-soft: #6d6e71;
    --mark-grey: #a7a9ac;
  }
  * { margin: 0; padding: 0; box-sizing: border-box; }
  html, body { width: 1200px; height: 800px; overflow: hidden; }
  body {
    background: var(--backdrop);
    font-family: "Montserrat", sans-serif;
    color: var(--ink);
    position: relative;
  }
  .card {
    position: absolute;
    background: var(--card);
    border-radius: 34px;
    box-shadow: 0 18px 40px rgba(0, 60, 100, 0.25);
    display: flex;
    flex-direction: column;
    align-items: center;
    justify-content: center;
    text-align: center;
  }
  .card--front { left: 60px; top: 230px; width: 580px; height: 340px; }
  .card--back { left: 720px; top: 110px; width: 380px; height: 580px; }

  .brand { display: flex; align-items: center; gap: 14px; margin-bottom: 22px; }
  .brand__dot {
    width: 38px; height: 38px; border-radius: 50%;
    border: 2px solid var(--mark-grey);
  }
  .brand__name {
    font-weight: 300;
    color: var(--mark-grey);
    text-transform: uppercase;
    letter-spacing: 0.08em;
    line-height: 1.15;
    text-align: left;
  }
  .card--front .brand__name { font-size: 26px; }
  .card--back .brand { flex-direction: column; gap: 16px; margin-bottom: 26px; }
  .card--back .brand__dot { width: 64px; height: 64px; }
  .card--back .brand__name { font-size: 30px; text-align: center; }

  .doctor { font-size: 17px; font-weight: 400; letter-spacing: 0.03em; }
  .doctor__post { font-size: 9px; letter-spacing: 0.06em; margin-left: 4px; }
  .diploma { font-size: 14px; color: var(--brand-blue); margin-top: 6px; letter-spacing: 0.02em; }
  .divider { width: 18px; height: 2px; background: var(--brand-blue); margin: 14px auto; }
  .card--back .divider { width: 34px; margin: 20px auto; }
  .contact { list-style: none; font-size: 14px; line-height: 1.7; letter-spacing: 0.03em; }
  .contact__web span { color: var(--brand-blue); }

  .tagline { font-size: 15px; color: var(--ink-soft); letter-spacing: 0.02em; }
  .services { list-style: none; font-size: 13.5px; line-height: 1.75; color: var(--ink); letter-spacing: 0.01em; }
</style>
</head>
<body>
  <section class="card card--front" aria-label="Business card front">
    <div class="brand">
      <span class="brand__dot"></span>
      <span class="brand__name">Moravel<br>Aesthetic Doctor</span>
    </div>
    <p class="doctor">Dr.Elise Varnov<span class="doctor__post">MRCPCH MD</span></p>
    <p class="diploma">Australasian Diploma of Aesthetic Medicine</p>
    <div class="divider"></div>
    <ul class="contact">
      <li>0800 457 319</li>
      <li>elise@moravel.co.nz</li>
      <li class="contact__web">www.<span>moravel</span>.co.nz</li>
    </ul>
  </section>

  <section class="card card--back" aria-label="Business card back">
    <div class="brand">
      <span class="brand__dot"></span>
      <span class="brand__name">Moravel<br>Aesthetic Doctor</span>
    </div>
    <p class="tagline">Home and Spa Based Treatments</p>
    <div class="divider"></div>
    <ul class="services">
      <li>Dermal injectables I Plasma facials</li>
      <li>Home and Spa Based Treatments</li>
      <li>Microneedling I Skin boosters</li>
      <li>Excessive sweating</li>
    </ul>
  </section>
</body>
</html>
```